Creative, fresh business card design for Ripplecraft Facades

We need a fresh, creative business card design for Ripplecraft Facades. We are the manufacturer of Ripplecraft Facades in Australia. Wall panels are 2400 x 1200mm panels made from MDF and feature 3D patterns on the face of the panel. The colours to be used are green, silver/grey and white RGB
Red 187
Green 207
Blue 65.

An idea is to possibly use a watermark of one of our designs as a background (like on the "Grids" design on the left hand side of page 2 of our brochure).

Target Market(s)

Interior designers, architects, builders and home renovators

Industry/Entity Type

Business

Contact Information for Business Card

Details to go on the card are:
Our logo (attached),
Slogan: "Decorative panels for interiors and exteriors",
Contact name,
Position,
Mobile phone number,
Business address,
Business phone,
Business fax,
Website and
Email address.

I have attached a few images of our panels and our brochure for reference.

The colours of the business card should feature our logo colours which are: RGB
Red 187
Green 207
Blue 65

Requirements
Must have
• Very modern fonts and design. Some of the designs shown especially the "Prisms" design which is a popular design.
Nice to have
• Creative but simple design. Very contemporary.
Should not have
• Anything ornate or old fashioned.

```html
<!DOCTYPE html>
<html lang="en">
<head>
<meta charset="utf-8">
<title>Ripplecraft Facades – Business Card</title>
<link href="https://fonts.googleapis.com/css2?family=Didact+Gothic&display=swap" rel="stylesheet">
<style>
  :root {
    --page-bg: #e9e7e2;
    --card-black: #161616;
    --card-black-2: #242424;
    --lime: #bbcf41;
    --silver: #b9b9b9;
    --text-light: #d6d6d6;
    --text-muted: #9a9a9a;
  }
  html, body {
    margin: 0;
    width: 1200px;
    height: 1022px;
    overflow: hidden;
    background: var(--page-bg);
    font-family: "Didact Gothic", "Century Gothic", sans-serif;
  }
  .business-card {
    position: absolute;
    left: 160px;
    top: 259px;
    width: 880px;
    height: 503px;
    border-radius: 6px;
    overflow: hidden;
    box-shadow: 0 18px 40px rgba(0,0,0,.35);
  }
  .card-texture {
    position: absolute;
    inset: 0;
    background: radial-gradient(circle at 35% 40%, var(--card-black-2), var(--card-black) 70%);
  }
  .brand {
    position: absolute;
    left: 70px;
    top: 200px;
    width: 340px;
  }
  .brand-name {
    display: flex;
    align-items: center;
    gap: 14px;
    color: var(--lime);
    font-size: 34px;
    line-height: 1.1;
  }
  .brand-square {
    width: 30px;
    height: 30px;
    background: var(--lime);
    flex: none;
  }
  .brand-band {
    margin-top: 14px;
    height: 4px;
    background: var(--silver);
  }
  .slogan {
    margin-top: 14px;
    color: var(--text-muted);
    font-size: 19px;
    letter-spacing: 3px;
    line-height: 1.35;
  }
  .divider {
    position: absolute;
    left: 450px;
    top: 100px;
    width: 2px;
    height: 230px;
    background: var(--lime);
  }
  .contact {
    position: absolute;
    left: 482px;
    top: 92px;
  }
  .person-name {
    color: var(--lime);
    font-size: 34px;
    letter-spacing: 1px;
    margin: 0;
  }
  .person-role {
    color: var(--text-muted);
    font-size: 19px;
    letter-spacing: 2px;
    margin: 4px 0 18px;
  }
  .contact-list {
    list-style: none;
    margin: 0;
    padding: 0;
  }
  .contact-list li {
    display: flex;
    align-items: center;
    gap: 14px;
    color: var(--text-light);
    font-size: 19px;
    letter-spacing: 2px;
    height: 32px;
  }
  .contact-list svg {
    width: 18px;
    height: 18px;
    flex: none;
  }
  .address {
    position: absolute;
    left: 482px;
    top: 420px;
    color: var(--text-muted);
    font-size: 19px;
    letter-spacing: 2px;
  }
</style>
</head>
<body>
  <div class="business-card">
    <div class="card-texture" role="img" aria-label="Faint embossed ripple panel pattern across the black card"></div>

    <div class="brand">
      <div class="brand-name"><span class="brand-square"></span>Ripplecraft Facades</div>
      <div class="brand-band"></div>
      <p class="slogan">decorative panels for<br>interiors &amp; landscapes</p>
    </div>

    <div class="divider"></div>

    <div class="contact">
      <h1 class="person-name">Leon Varga</h1>
      <p class="person-role">President</p>
      <ul class="contact-list">
        <li>
          <svg viewBox="0 0 18 18" aria-hidden="true"><rect x="5" y="1" width="8" height="16" rx="1.5" fill="none" stroke="var(--lime)" stroke-width="1.6"/><circle cx="9" cy="14" r="1" fill="var(--lime)"/></svg>
          310. 555. 0142
        </li>
        <li>
          <svg viewBox="0 0 18 18" aria-hidden="true"><path d="M4 2 l3 0 l1.5 4 l-2 1.5 a9 9 0 0 0 4 4 l1.5 -2 l4 1.5 l0 3 a2 2 0 0 1 -2 2 A14 14 0 0 1 2 4 a2 2 0 0 1 2 -2z" fill="var(--lime)"/></svg>
          310. 555. 0187
        </li>
        <li>
          <svg viewBox="0 0 18 18" aria-hidden="true"><rect x="4" y="1" width="10" height="6" fill="var(--lime)"/><rect x="1" y="7" width="16" height="7" rx="1" fill="var(--lime)"/><rect x="4" y="12" width="10" height="5" fill="var(--card-black)" stroke="var(--lime)" stroke-width="1.2"/></svg>
          310. 555. 0193
        </li>
        <li>
          <svg viewBox="0 0 18 18" aria-hidden="true"><rect x="1" y="3" width="16" height="12" fill="var(--lime)"/><path d="M1 3 l8 7 l8 -7" fill="none" stroke="var(--card-black)" stroke-width="1.4"/></svg>
          leon@ripplecraft.net
        </li>
        <li>
          <svg viewBox="0 0 18 18" aria-hidden="true"><circle cx="9" cy="9" r="7.5" fill="none" stroke="var(--lime)" stroke-width="1.6"/><ellipse cx="9" cy="9" rx="3.2" ry="7.5" fill="none" stroke="var(--lime)" stroke-width="1.2"/><line x1="1.5" y1="9" x2="16.5" y2="9" stroke="var(--lime)" stroke-width="1.2"/></svg>
          www.ripplecraft.net
        </li>
      </ul>
    </div>

    <p class="address">4120 Harbour Road, Westvale, CA 90411</p>
  </div>
</body>
</html>
```